Company Website Re-design for Software development consultancy

We would like our company website to be redesigned using our existing marketing collateral and website content as a guide

current site : www.brightkestrel.com.au

For the different pages types and content please base on the following site : https://www.quorvalabs.net/

We want a coded site - but will replace the content ourselves within the sections you provide to customise to our needs.

Target Market(s)

Medium to Large corporates needing software design and development services

Industry/Entity Type

Information Technology

Coding

Coded - Design and coding required

Number of Pages Required

5+ page

Font styles to use
Sans Serif

Colors
ec1f27
ffffff
000000

Requirements
Must have
• Align to colour scheme of existing collateral
• Include pages for the key areas of our busines - see : https://www.quorvalabs.net/
Nice to have
• image rotators - make the site interesting to the business visitor

```html
<!DOCTYPE html>
<html lang="en">
<head>
<meta charset="utf-8">
<title>Bright Kestrel – Building Software Better</title>
<link href="https://fonts.googleapis.com/css2?family=Open+Sans:wght@400;600;700&family=Roboto:wght@400;500;700;900&display=swap" rel="stylesheet">
<style>
:root{
  --red:#ec1f27;
  --black:#000000;
  --white:#ffffff;
  --ink:#1b1b1b;
  --grey-text:#555555;
  --light:#eeeeee;
  --band-grey:#e7e7e7;
  --footer-dark:#1e1a1a;
}
*{margin:0;padding:0;box-sizing:border-box}
html,body{width:1200px;height:3922px;overflow:hidden}
body{position:relative;background:var(--white);font-family:"Open Sans",sans-serif;color:var(--ink)}
.abs{position:absolute}
h1,h2,h3,h4{font-family:"Roboto",sans-serif}
.btn-red{position:absolute;background:var(--red);color:var(--white);font-family:"Roboto",sans-serif;font-weight:500;font-size:17px;letter-spacing:.5px;display:flex;align-items:center;justify-content:center;text-transform:uppercase}

/* header & hero */
.hero{left:0;top:0;width:1200px;height:518px;background:linear-gradient(90deg,#f7f7f7 0%,#eef0f1 45%,#dfe3e6 100%)}
.hero-photo{left:500px;top:0;width:700px;height:518px;background:linear-gradient(135deg,#c9ced2 0%,#e6e1da 40%,#6d6a68 75%,#2f2f33 100%)}
.brand{left:98px;top:32px;font-family:"Roboto",sans-serif;font-weight:900;font-size:40px;color:var(--black);letter-spacing:.5px}
.nav{right:100px;top:42px;display:flex;gap:34px;font-family:"Roboto",sans-serif;font-weight:500;font-size:15px;color:var(--black)}
.hero-title{left:98px;top:135px;font-size:56px;font-weight:500;color:var(--red);line-height:1}
.hero-sub{left:98px;top:197px;font-size:40px;font-weight:400;color:var(--black);line-height:1.1}
.hero-copy{left:100px;top:262px;width:420px;font-size:15px;line-height:31px;color:var(--black)}
.hero .btn-red{left:100px;top:358px;width:180px;height:48px}
.dots{left:102px;top:450px;display:flex;gap:12px}
.dots span{width:9px;height:9px;border-radius:50%;background:var(--red);opacity:.55}
.dots span:first-child{opacity:1}

/* contact band */
.band{left:0;top:518px;width:1200px;height:125px;background:var(--red);color:var(--white)}
.band h3{position:absolute;left:100px;top:34px;font-size:22px;font-weight:500}
.band p{position:absolute;left:100px;top:68px;font-size:14px}
.band .cta{position:absolute;left:850px;top:39px;width:248px;height:50px;background:var(--black);color:var(--white);font-family:"Roboto",sans-serif;font-size:17px;letter-spacing:3px;display:flex;align-items:center;justify-content:center}

/* who we are */
.section-title{width:1200px;left:0;text-align:center;font-size:40px;font-weight:700;color:var(--black)}
.who-copy{left:170px;top:810px;width:860px;text-align:center;font-size:14px;line-height:30px;color:#333}
.who-btn{left:518px;top:970px;width:164px;height:50px}

/* three faces */
.faces-title{left:100px;top:1112px;font-size:40px;font-weight:700;line-height:48px;color:var(--black)}
.faces-tag{left:100px;top:1215px;font-size:13px;color:#aaa}
.face{left:100px;width:360px;height:90px}
.face .icon{position:absolute;left:0;top:0;width:60px;height:60px;background:var(--red);display:flex;align-items:center;justify-content:center}
.face h4{position:absolute;left:80px;top:-2px;font-size:16px;color:var(--red);font-weight:700}
.face p{position:absolute;left:80px;top:22px;width:285px;font-size:12.5px;line-height:22px;color:#555}
.faces-photo{left:468px;top:1180px;width:305px;height:345px;background:linear-gradient(180deg,#f5f5f5 0%,#dfe4ea 50%,#bfc6ce 100%);border-radius:4px}
.faces-copy{left:797px;top:1262px;width:303px;font-size:14px;line-height:31px;text-align:justify;color:#333}

/* clients */
.clients-bg{left:0;top:1715px;width:1200px;height:455px;background:var(--band-grey)}
.clients-photo{left:0;top:1715px;width:580px;height:455px}
.client{width:180px;text-align:center;font-family:"Roboto",sans-serif;font-weight:700;font-size:21px;color:#8d8d8d;display:flex;align-items:center;justify-content:center;gap:8px}
.client i{display:inline-block;width:14px;height:14px;background:#8d8d8d;border-radius:50%}

/* leadership */
.leaders{left:0;top:2170px;width:1200px;height:580px;background:var(--white)}
.leader{width:440px;height:120px}
.leader .avatar{position:absolute;left:0;top:0;width:116px;height:116px;border-radius:50%;background:radial-gradient(circle at 50% 40%,#d9b8a2 0%,#9a7c6a 55%,#4c4340 100%)}
.leader h4{position:absolute;left:150px;top:12px;font-size:22px;font-weight:500;color:var(--black)}
.leader h4 em{font-style:italic;font-size:14px;color:var(--red);font-weight:700;margin-left:14px;letter-spacing:.5px}
.leader p{position:absolute;left:150px;top:50px;width:250px;font-size:13px;line-height:24px;color:#555}
.arrow{top:2495px}

/* news */
.news{left:0;top:2750px;width:1200px;height:714px;background:var(--light)}
.card{background:var(--white);position:absolute}
.card h4{font-size:15px;font-weight:700;line-height:24px;color:var(--black);text-transform:uppercase}
.card p{font-size:12.5px;line-height:22px;color:#555}
.card .more{color:var(--red)}
.card .meta{font-size:10px;color:#555;margin-top:8px}
.card .meta b{color:var(--red);font-weight:600}
.card .tag{position:absolute;right:8px;top:8px;width:20px;height:20px;background:var(--red);border-radius:3px}
.news-img{position:absolute;background:linear-gradient(135deg,#8e9aa4,#dcdfe2 50%,#5b646b)}

/* footer */
.footer{left:0;top:3464px;width:1200px;height:371px;background:var(--footer-dark);color:var(--white)}
.footer h4{position:absolute;top:86px;font-size:20px;font-weight:500}
.footer ul{position:absolute;top:132px;list-style:none;font-size:14px;line-height:31px}
.footer ul li::before{content:"";display:inline-block;width:5px;height:5px;background:var(--white);border-radius:50%;margin-right:20px;vertical-align:middle}
.field{position:absolute;left:100px;width:266px;height:29px;background:var(--white);color:#999;font-size:12px;padding:6px 10px}
.contact-row{position:absolute;left:865px;font-size:14px;display:flex;align-items:center;gap:16px}

.bottom{left:0;top:3835px;width:1200px;height:87px;background:var(--white)}
.social{left:526px;top:19px;display:flex;gap:10px}
.social span{width:20px;height:20px;border-radius:50%;background:#1e5aa8}
.copyright{left:0;top:50px;width:1200px;text-align:center;font-size:12px;color:#555}
</style>
</head>
<body>

<!-- header and hero -->
<section class="abs hero">
  <div class="abs hero-photo" role="img" aria-label="Photo of two colleagues working together at a laptop in a bright office"></div>
  <div class="abs brand">BRIGHT KESTREL</div>
  <nav class="abs nav"><span>Solutions</span><span>Services</span><span>Industries</span><span>Resources</span><span>Clients</span><span>Company</span></nav>
  <h1 class="abs hero-title">Bright Kestrel</h1>
  <h2 class="abs hero-sub">Building Software Better</h2>
  <p class="abs hero-copy">We combine a solid knowledge of computer science with a practical, pragmatic approach to delivering software.</p>
  <div class="btn-red">Learn More</div>
  <div class="abs dots"><span></span><span></span><span></span><span></span></div>
</section>

<section class="abs band">
  <h3>Want to say Hey or find out more?</h3>
  <p>Lorem ipsum dolor sit amet, consectetur adipiscing elit, sed do eiusmod tempor</p>
  <div class="cta">GET IN TOUCH</div>
</section>

<!-- who we are -->
<h2 class="abs section-title" style="top:736px">Who We &nbsp;Are</h2>
<p class="abs who-copy">Sed ut perspiciatis unde omnis iste natus error sit voluptatem accusantium doloremque laudantium, totam rem voluptatem quia voluptas sit aspernatur aut odit aut fugit, sed quia consequuntur magni dolores eos qui ratione voluptatem sequi nesciunt. Neque porro quisquam est, qui dolorem ipsum quia dolor sit amet, consectetur, adipisci velit, sed quia non numquam eius modi tempora incidunt ut labore et dolore magnam aliquam quaerat voluptatem.</p>
<div class="btn-red who-btn">Learn More</div>

<!-- three faces -->
<h2 class="abs faces-title">The Three Faces of<br>Bright Kestrel</h2>
<p class="abs faces-tag">We are all about building software better.</p>

<div class="abs face" style="top:1275px">
  <div class="icon"><svg width="28" height="28" viewBox="0 0 28 28"><circle cx="14" cy="9" r="6" fill="#fff"/><path d="M3 27c0-7 5-11 11-11s11 4 11 11z" fill="#fff"/></svg></div>
  <h4>Consulting</h4>
  <p>Up-skill your team by using our consultants - For either short or long term engagements</p>
</div>
<div class="abs face" style="top:1368px">
  <div class="icon"><svg width="28" height="28" viewBox="0 0 28 28"><path d="M3 8h7a4 4 0 1 1 8 0h7v17H3z" fill="#fff"/></svg></div>
  <h4>Projects</h4>
  <p>We can deliver a large project on a fixed price basis at a quality standard you won't believe</p>
</div>
<div class="abs face" style="top:1465px">
  <div class="icon"><svg width="28" height="28" viewBox="0 0 28 28"><rect x="3" y="4" width="22" height="6" fill="#fff"/><rect x="5" y="12" width="18" height="13" fill="#fff"/><rect x="11" y="15" width="6" height="2" fill="#ec1f27"/></svg></div>
  <h4>Impress</h4>
  <p>Our product, inForge, allows you to skip the development cycle and turn an excel spreadsheet directly into either a web service or a web site</p>
</div>

<div class="abs faces-photo" role="img" aria-label="Photo of a consultant in shirt and tie holding a laptop"></div>
<p class="abs faces-copy">After spending more than twenty years each in the industry, including seven years in New York building electronic trading systems for Hartwell Grant – the founders realised that there was a distinct lack in the market of people focusing on how software is developed – not just solving the business problem, but automating the development itself to increase both productivity and quality.</p>

<!-- clients -->
<h2 class="abs section-title" style="top:1644px">Our Clients</h2>
<div class="abs clients-bg"></div>
<svg class="abs clients-photo" viewBox="0 0 580 455" role="img" aria-label="Photo of a presenter at a whiteboard during a team meeting">
  <defs><linearGradient id="meetTone" x1="0" y1="0" x2="1" y2="1"><stop offset="0" stop-color="#cfc8c0"/><stop offset=".5" stop-color="#a8a29b"/><stop offset="1" stop-color="#4b4541"/></linearGradient></defs>
  <polygon points="0,0 580,0 470,455 0,455" fill="url(#meetTone)"/>
</svg>
<div class="abs client" style="left:555px;top:1826px">Palmreach</div>
<div class="abs client" style="left:755px;top:1826px"><i></i>Tidemark</div>
<div class="abs client" style="left:958px;top:1826px">Norvella</div>
<div class="abs client" style="left:555px;top:1927px">Norvella</div>
<div class="abs client" style="left:755px;top:1927px"><i></i>Cloudharbor</div>
<div class="abs client" style="left:958px;top:1927px">Palmreach</div>
<div class="abs client" style="left:555px;top:2032px"><i></i>Mailverge</div>
<div class="abs client" style="left:755px;top:2032px"><i></i>Tidemark</div>

<!-- leadership -->
<section class="abs leaders">
  <h2 class="abs section-title" style="top:84px">Meet Our Leadership Team</h2>
  <div class="abs leader" style="left:146px;top:203px">
    <div class="avatar" role="img" aria-label="Portrait of Owen Marsh"></div>
    <h4>Owen Marsh<em>PARTNER</em></h4>
    <p>Owen's one of the Best developers on the planet</p>
  </div>
  <div class="abs leader" style="left:645px;top:203px">
    <div class="avatar" role="img" aria-label="Portrait of Lucas Brandt"></div>
    <h4>Lucas Brandt<em>PARTNER</em></h4>
    <p>Lucas's been running software projects for 20 years</p>
  </div>
  <div class="abs leader" style="left:146px;top:363px">
    <div class="avatar" role="img" aria-label="Portrait of Simon Pryce"></div>
    <h4>Simon Pryce<em>PARTNER</em></h4>
    <p>Simon codes for fun as much as he does for work</p>
  </div>
  <div class="abs leader" style="left:645px;top:363px">
    <div class="avatar" role="img" aria-label="Portrait of Min Seo"></div>
    <h4>Min Seo<em>PARTNER</em></h4>
    <p>Lorem ipsum dolor sit amet, consectetur adipiscing elit, sed do eiusmod</p>
  </div>
</section>
<svg class="abs arrow" style="left:38px" width="18" height="26" viewBox="0 0 18 26"><path d="M15 2 4 13l11 11" fill="none" stroke="#333" stroke-width="4"/></svg>
<svg class="abs arrow" style="left:1142px" width="18" height="26" viewBox="0 0 18 26"><path d="M3 2l11 11L3 24" fill="none" stroke="#333" stroke-width="4"/></svg>

<!-- news -->
<section class="abs news">
  <h2 class="abs section-title" style="top:94px">Latest News and Insights</h2>

  <div class="card" style="left:99px;top:178px;width:568px;height:436px">
    <div class="tag"></div>
    <div style="position:absolute;left:14px;top:14px;width:520px">
      <h4>Lorem ipsum dolor sit amet,<br>consectetur adipi</h4>
      <p style="margin-top:6px">Sed ut perspiciatis unde omnis iste natus error sit voluptatem ... <span class="more" style="margin-left:24px">Read More</span></p>
      <div class="meta"><b>&#9650;</b> 3 Like &nbsp;|&nbsp; <b>&#9650;</b> 7 Comment &nbsp;|&nbsp; <b>&lt;</b> Share</div>
    </div>
    <div class="news-img" style="left:0;top:117px;width:568px;height:319px" role="img" aria-label="Photo of business people meeting around a conference table"></div>
  </div>

  <div class="card" style="left:680px;top:178px;width:418px;height:209px">
    <div class="tag"></div>
    <div class="news-img" style="left:0;top:0;width:172px;height:209px;background:linear-gradient(135deg,#3a3f45,#9aa2a8 50%,#2b2e31)" role="img" aria-label="Photo of a laptop keyboard on a desk"></div>
    <div style="position:absolute;left:192px;top:20px;width:200px">
      <h4>Lorem ipsum dolor<br>sit amet,</h4>
      <p style="margin-top:10px">Sed ut perspiciatis unde omnis iste natus error sit voluptatem ... <span class="more">Read More</span></p>
      <div class="meta"><b>&#9650;</b> 3 Like | <b>&#9650;</b> 7 Comment | <b>&lt;</b> Share</div>
    </div>
  </div>

  <div class="card" style="left:680px;top:400px;width:418px;height:214px">
    <div class="tag"></div>
    <div class="news-img" style="left:0;top:0;width:172px;height:214px;background:linear-gradient(135deg,#1c2a3c,#4f6f8f 55%,#101820)" role="img" aria-label="Photo of a person lit by a computer screen"></div>
    <div style="position:absolute;left:192px;top:20px;width:200px">
      <h4>Lorem ipsum dolor<br>sit amet,</h4>
      <p style="margin-top:10px">Sed ut perspiciatis unde omnis iste natus error sit voluptatem ... <span class="more">Read More</span></p>
      <div class="meta"><b>&#9650;</b> 3 Like | <b>&#9650;</b> 7 Comment | <b>&lt;</b> Share</div>
    </div>
  </div>
</section>

<!-- footer -->
<footer class="abs footer">
  <svg class="abs" style="left:0;top:0" width="460" height="371" viewBox="0 0 460 371"><polygon points="0,0 457,0 405,371 0,371" fill="#ec1f27"/></svg>
  <h4 style="left:100px">Get In Touch</h4>
  <p class="abs" style="left:100px;top:142px;font-size:13px">Bright Kestrel is based in Sydney Australia</p>
  <div class="field" style="top:190px">Name</div>
  <div class="field" style="top:235px">Email</div>
  <p class="abs" style="left:100px;top:284px;font-size:14px;font-weight:700;text-decoration:underline">Subscribe</p>

  <h4 style="left:481px">Quick links</h4>
  <ul style="left:485px"><li>Home</li><li>About Us</li><li>Services</li><li>Blog</li><li>Contact Us</li></ul>

  <h4 style="left:674px">Other links</h4>
  <ul style="left:678px"><li>All</li><li>Solution</li><li>Organization</li><li>Industries</li><li>Resources</li></ul>

  <h4 style="left:865px">Contact Us</h4>
  <div class="contact-row" style="top:136px"><svg width="14" height="18" viewBox="0 0 14 18"><path d="M7 0a7 7 0 0 0-7 7c0 5 7 11 7 11s7-6 7-11a7 7 0 0 0-7-7z" fill="#fff"/><circle cx="7" cy="7" r="2.5" fill="#1e1a1a"/></svg>42 Harbour Lane, Sydney 2000</div>
  <div class="contact-row" style="top:167px"><svg width="16" height="12" viewBox="0 0 16 12"><rect width="16" height="12" fill="#fff"/><path d="M0 0l8 7 8-7" fill="none" stroke="#1e1a1a" stroke-width="1.5"/></svg>info@brightkestrel.com.au</div>
  <div class="contact-row" style="top:198px"><svg width="16" height="16" viewBox="0 0 16 16"><path d="M3 0l3 4-2 2c1 2 4 5 6 6l2-2 4 3-2 3C7 16 0 9 0 3z" fill="#fff"/></svg>0291847730</div>
</footer>

<div class="abs bottom">
  <div class="abs social"><span></span><span style="background:#d8412f"></span><span style="background:#0e76a8"></span><span style="background:#1da1f2"></span><span style="background:#3b5b8c"></span></div>
  <p class="abs copyright">Copyright © 2018 Bright Kestrel All Rights Reserved | Terms | Policy.</p>
</div>

</body>
</html>
```